GJ & DW Fencing Pty Ltd

We already have an existing logo created by Pixel Harbour however we have restructured to a company. We would like someone to add Pty Ltd to our business name please.

Colors

Designer to choose only greyscale colors for use in the design.

```html
<!DOCTYPE html>
<html lang="en">
<head>
<meta charset="utf-8">
<title>GJ &amp; DW Fencing Pty Ltd – Business Cards</title>
<link href="https://fonts.googleapis.com/css2?family=Lato:wght@400&family=Libre+Baskerville:wght@700&display=swap" rel="stylesheet">
<style>
  :root {
    --backdrop: #d9d9d9;
    --card-light: #ffffff;
    --card-dark: #17161b;
    --ink: #111111;
    --ink-soft: #2a2a2a;
    --rule: #444444;
    --paper-text: #f4f4f4;
  }
  * { margin: 0; padding: 0; box-sizing: border-box; }
  html, body { width: 1200px; height: 844px; overflow: hidden; }
  body {
    background: var(--backdrop);
    position: relative;
    font-family: "Lato", Arial, sans-serif;
  }
  .card {
    position: absolute;
    top: 279px;
    width: 500px;
    height: 286px;
    box-shadow: 0 6px 18px rgba(0,0,0,0.25);
  }
  .card-front { left: 70px; background: var(--card-light); color: var(--ink); }
  .card-back { left: 630px; background: var(--card-dark); color: var(--paper-text); }

  .brand {
    position: absolute;
    text-align: center;
    font-family: "Libre Baskerville", Georgia, serif;
    font-weight: 700;
    line-height: 1.15;
    text-transform: uppercase;
  }
  .brand-name { font-size: 26px; letter-spacing: 0.5px; display: block; }
  .brand-suffix { font-size: 12px; letter-spacing: 2px; display: block; }
  .card-front .brand { right: 34px; top: 44px; }
  .card-back .brand { left: 0; right: 0; top: 100px; }
  .card-back .brand-suffix::before,
  .card-back .brand-suffix::after {
    content: ""; display: inline-block; width: 40px; height: 1px;
    background: var(--paper-text); vertical-align: middle; margin: 0 10px;
  }

  .name-rule {
    position: absolute; left: 176px; right: 34px; top: 134px;
    height: 1px; background: var(--rule);
  }
  .holder-name {
    position: absolute; left: 34px; top: 124px;
    font-family: "Libre Baskerville", Georgia, serif;
    font-weight: 700; font-size: 15px; letter-spacing: 0.5px;
    text-transform: uppercase; background: var(--card-light); padding-right: 8px;
  }
  .contact-list {
    position: absolute; left: 34px; top: 178px; list-style: none;
  }
  .contact-item {
    display: flex; align-items: center; gap: 8px;
    font-size: 14px; color: var(--ink-soft); height: 26px;
  }
  .contact-icon { width: 18px; height: 18px; flex: none; }
</style>
</head>
<body>
  <section class="card card-front" aria-label="Business card front">
    <div class="brand">
      <span class="brand-name">GJ &amp; DW Fencing</span>
      <span class="brand-suffix">Pty Ltd</span>
    </div>
    <div class="name-rule"></div>
    <p class="holder-name">Tom Carraway</p>
    <ul class="contact-list">
      <li class="contact-item">
        <svg class="contact-icon" viewBox="0 0 18 18" aria-hidden="true">
          <circle cx="9" cy="9" r="9" fill="#111"/>
          <path d="M5.5 5.5c0 4 3 7 7 7l1-1.5-2-1-1 1c-1.2-.5-2.3-1.6-2.8-2.8l1-1-1-2z" fill="#fff"/>
        </svg>
        044 5182907
      </li>
      <li class="contact-item">
        <svg class="contact-icon" viewBox="0 0 18 18" aria-hidden="true">
          <circle cx="9" cy="9" r="9" fill="#111"/>
          <rect x="4.5" y="6" width="9" height="6.5" fill="none" stroke="#fff" stroke-width="1.2"/>
          <path d="M4.5 6l4.5 4 4.5-4" fill="none" stroke="#fff" stroke-width="1.2"/>
        </svg>
        gjdwfencing@mailbox.com
      </li>
      <li class="contact-item">
        <svg class="contact-icon" viewBox="0 0 18 18" aria-hidden="true">
          <circle cx="9" cy="9" r="9" fill="#111"/>
          <path d="M9 14.5s-3.5-3.6-3.5-6.3a3.5 3.5 0 0 1 7 0c0 2.7-3.5 6.3-3.5 6.3z" fill="#fff"/>
          <circle cx="9" cy="8.2" r="1.3" fill="#111"/>
        </svg>
        PO Box 418 Ridgefield WA 6390
      </li>
    </ul>
  </section>

  <section class="card card-back" aria-label="Business card back">
    <div class="brand">
      <span class="brand-name">GJ &amp; DW Fencing</span>
      <span class="brand-suffix">Pty Ltd</span>
    </div>
  </section>
</body>
</html>
```